Business Card Design for BrightvaleMedia.com

--I need a business card design for my company BrightvaleMedia.com

I have attached my logo...I want the brightvale media logo on the front of the business card, and then I want The Quillstone Chief on the back of it with my information.

I would like to see a light colored background as well as a dark colored background

FRONT:
BRIGHTVALE MEDIA LOGO
248 N. Larkmoor
3rd Floor
San Diego CA 92173
www.BrightvaleMedia.com

Advanced Website & App Development
Websites, Apps, Online Voucher Systems

Leading Edge Marketing Services
SMS, VB, SMM, SEM,

BACK:
QUILLSTONE CHIEF LOGO
Dorian Pelletta
The Quillstone Chief
Call Or Text: 619-555-0148
Dorian@QuillstoneChief.example
www.QuillstoneChief.example

Target Market(s)

small business owners

Industry/Entity Type

Business Consultant

Contact Information for Business Card

FRONT:
BRIGHTVALE MEDIA LOGO
248 N. Larkmoor
3rd Floor
San Diego CA 92173
www.BrightvaleMedia.com

SMS, VB, SMM, SEM,

BACK:
QUILLSTONE CHIEF LOGO
Dorian Pelletta
The Quillstone Chief
Dorian@QuillstoneChief.example
www.QuillstoneChief.example

Requirements
Must have
• add this quote on it somewhere, anywhere,preferrably on back
• "The Fastest Way To Success Is To Take Action”
• — Dorian Pelletta, Quillstone Chief
Nice to have
• open
Should not have
• red

```html
<!DOCTYPE html>
<html lang="en">
<head>
<meta charset="utf-8">
<title>Brightvale Media Business Card</title>
<link href="https://fonts.googleapis.com/css2?family=Source+Sans+3:ital,wght@0,400;0,600;1,400&display=swap" rel="stylesheet">
<style>
  :root {
    --stage: #3a3a3c;
    --card-dark: #6b6c70;
    --card-light: #ffffff;
    --brand-blue: #1a6fa8;
    --ink-grey: #5a5b5e;
    --ink-dark: #3e3f42;
    --band-grey: #6b6c70;
    --on-dark: #ffffff;
  }
  * { margin: 0; padding: 0; box-sizing: border-box; }
  html, body {
    width: 1105px;
    height: 1200px;
    overflow: hidden;
    background: var(--stage);
    font-family: "Source Sans 3", "Myriad Pro", sans-serif;
  }
  .canvas {
    position: relative;
    width: 1105px;
    height: 1200px;
  }
  .card {
    position: absolute;
    left: 196px;
    width: 720px;
    height: 411px;
    overflow: hidden;
  }
  /* Front */
  .card-front {
    top: 146px;
    background: var(--card-dark);
    color: var(--on-dark);
  }
  .front-wordmark {
    position: absolute;
    left: 61px;
    top: 66px;
    font-size: 34px;
    font-weight: 400;
    letter-spacing: 3.5px;
    line-height: 1;
  }
  .front-details {
    position: absolute;
    left: 61px;
    top: 140px;
    font-size: 19px;
    line-height: 27px;
  }
  .front-details .web { font-weight: 600; }
  .front-details .group { margin-bottom: 12px; }

  /* Back */
  .card-back {
    top: 602px;
    background: var(--card-light);
  }
  .back-wordmark {
    position: absolute;
    left: 41px;
    top: 60px;
    font-size: 36px;
    font-weight: 600;
    letter-spacing: 2.5px;
    line-height: 1;
    color: var(--brand-blue);
  }
  .quote {
    position: absolute;
    left: 41px;
    top: 128px;
    width: 400px;
    color: var(--ink-grey);
  }
  .quote-text {
    font-size: 17px;
    font-style: italic;
    line-height: 24px;
  }
  .quote-source {
    font-size: 15px;
    line-height: 22px;
    margin-top: 2px;
  }
  .person {
    position: absolute;
    right: 41px;
    top: 238px;
    text-align: right;
  }
  .person-name {
    font-size: 26px;
    font-weight: 600;
    color: var(--brand-blue);
    line-height: 32px;
  }
  .person-title {
    font-size: 20px;
    color: var(--ink-grey);
    line-height: 28px;
  }
  .divider {
    position: absolute;
    left: 41px;
    right: 41px;
    top: 308px;
    height: 2px;
    background: var(--brand-blue);
  }
  .contact-list {
    position: absolute;
    left: 41px;
    top: 320px;
    list-style: none;
    font-size: 19px;
    line-height: 27px;
    color: var(--ink-grey);
  }
  .contact-list li { display: flex; align-items: center; gap: 10px; }
  .contact-list svg { width: 18px; height: 18px; fill: var(--brand-blue); }
  .back-web {
    position: absolute;
    right: 41px;
    top: 347px;
    font-size: 19px;
    line-height: 27px;
    font-weight: 600;
    color: var(--ink-dark);
  }
  .base-band {
    position: absolute;
    left: 0;
    bottom: 0;
    width: 720px;
    height: 12px;
  }
</style>
</head>
<body>
<main class="canvas">

  <section class="card card-front" aria-label="Business card front">
    <div class="front-wordmark">BRIGHTVALE MEDIA</div>
    <div class="front-details">
      <div class="group">
        <p>248 N. Larkmoor, 3rd Floor</p>
        <p>San Diego CA 92173</p>
        <p class="web">www.BrightvaleMedia.com</p>
      </div>
      <div class="group">
        <p>Advanced Website &amp; App Development</p>
        <p>Websites • Apps • Online Voucher Systems</p>
      </div>
      <div class="group">
        <p>Leading Edge Marketing Services</p>
        <p>SMS • VB • SMM • SEM</p>
      </div>
    </div>
  </section>

  <section class="card card-back" aria-label="Business card back">
    <div class="back-wordmark">QUILLSTONE CHIEF</div>

    <blockquote class="quote">
      <p class="quote-text">“The Fastest Way To Success Is To Take Action”</p>
      <p class="quote-source">— Dorian Pelletta, Quillstone Chief</p>
    </blockquote>

    <div class="person">
      <p class="person-name">Dorian Pelletta</p>
      <p class="person-title">The Quillstone Chief</p>
    </div>

    <div class="divider"></div>

    <ul class="contact-list">
      <li>
        <svg viewBox="0 0 24 24" aria-hidden="true"><path d="M6.6 10.8a15.1 15.1 0 0 0 6.6 6.6l2.2-2.2c.3-.3.7-.4 1-.2 1.1.4 2.3.6 3.6.6.6 0 1 .4 1 1V20c0 .6-.4 1-1 1A17 17 0 0 1 3 4c0-.6.4-1 1-1h3.5c.6 0 1 .4 1 1 0 1.3.2 2.5.6 3.6.1.3 0 .7-.2 1z"/></svg>
        <span>619-555-0148</span>
      </li>
      <li>
        <svg viewBox="0 0 24 24" aria-hidden="true"><path d="M2 6h20v12H2z"/><path d="M2 6l10 7 10-7" fill="none" stroke="#fff" stroke-width="1.6"/></svg>
        <span>Dorian@QuillstoneChief.example</span>
      </li>
    </ul>

    <p class="back-web">www.QuillstoneChief.example</p>

    <svg class="base-band" viewBox="0 0 720 12" preserveAspectRatio="none" aria-hidden="true">
      <polygon points="0,0 476,0 471,12 0,12" fill="var(--brand-blue)"/>
      <polygon points="480,0 720,0 720,12 475,12" fill="var(--band-grey)"/>
    </svg>
  </section>

</main>
</body>
</html>
```